Summit Bodyform Gym Website

We need a website design for our gym.

Summit is the UAE's first calisthenics and parkour gym. The theme under which the gym revolves is that one does not require any machinery to workout as our bodies could be themselves the machinery. The gym is designed to be the more of a social hub rather than an "in-and-out" gym, where people come train, have fun, hang out and socialize for a few hours rather than just train for 60 minutes then leave. The gym is designed to be a big open space with lots of natural sunlight, natural wood and plants all over the place to create a natural and refreshing setting. We also use recycled material throughout the gym and recycle our waste as being green is part of our philosophy. We currently also have some of the world's top and most recognized calisthenics athletes working with us.

We would like our website to reflect all that as well as provide a simple, interactive and fun way for visitors to be able to get class and gym information, check out gym media and contact us for bookings.

Target Market(s)

Ages 15-35

Industry/Entity Type

Fitness

Coding

Coded - Design and coding required

Number of Pages Required

4 page

Font styles to use
Decorative

Colors
0792cd

Requirements
Must have
• Class descriptions
• Gym description
• Class schedules
• Trainer profiles
• Gym philosophy
• Contact Details
Nice to have
• A link to contact us directly for a free first trial class

```html
<!DOCTYPE html>
<html lang="en">
<head>
<meta charset="utf-8">
<title>Summit Bodyform Gym</title>
<link rel="stylesheet" href="https://fonts.googleapis.com/css2?family=Oswald:wght@400;500&family=Open+Sans:wght@400;600;700;800&display=swap">
<style>
:root{
  --blue:#0792cd;
  --blue-dark:#0679ad;
  --blue-head:#1590c4;
  --footer:#0a98c7;
  --footer-field:#19a9d8;
  --orange:#ef5a2a;
  --grey-band:#efefef;
  --grey-line:#d9d9d9;
  --text:#555;
  --text-dark:#333;
  --white:#fff;
  --photo-dark:#2a2f36;
  --photo-mid:#5b6470;
}
*{box-sizing:border-box;margin:0;padding:0}
html,body{width:1200px;height:2353px;overflow:hidden}
body{position:relative;background:var(--white);font-family:"Open Sans",Arial,sans-serif;color:var(--text)}
.abs{position:absolute}
.heading{font-family:"Oswald",Arial,sans-serif;font-weight:400;color:var(--blue-head);text-transform:uppercase;letter-spacing:.2px}
.btn{position:absolute;display:flex;align-items:center;justify-content:center;background:var(--blue);color:var(--white);font-weight:700;font-size:11px;letter-spacing:2.4px;text-transform:uppercase;border-radius:5px;box-shadow:0 2px 0 var(--blue-dark)}

/* header */
.brand{left:160px;top:18px;display:flex;align-items:center;gap:10px}
.brand-dot{width:22px;height:22px;border-radius:50%;background:var(--blue)}
.brand-name{font-weight:800;font-size:40px;color:var(--text-dark);letter-spacing:-1px}
.call-box{left:667px;top:27px;width:230px;height:62px;border:1px solid var(--grey-line);border-radius:6px;display:flex;align-items:center;padding-left:12px;gap:14px;background:var(--white)}
.call-icon{width:36px;height:36px;border-radius:50%;background:var(--blue);display:flex;align-items:center;justify-content:center}
.call-label{font-size:12px;letter-spacing:1.5px;color:var(--text)}
.call-number{font-size:19px;color:var(--blue);letter-spacing:1px}
.search-tab{left:919px;top:67px;width:118px;height:44px;background:var(--blue);border-radius:14px 14px 0 0;color:var(--white);font-size:10px;font-weight:700;display:flex;align-items:center;justify-content:center;gap:6px;padding-bottom:6px}
.main-nav{left:162px;top:110px;width:759px;height:42px;background:var(--blue);border-radius:0 0 14px 14px;display:flex;z-index:3;overflow:hidden}
.main-nav a{color:var(--white);text-decoration:none;font-size:10.5px;font-weight:700;text-transform:uppercase;display:flex;align-items:center;padding:0 11.5px;border-right:1px solid rgba(255,255,255,.25)}
.main-nav a.is-active{background:var(--blue-dark)}
.main-nav a:last-child{border-right:none}

/* hero */
.hero{left:0;top:110px;width:1200px;height:447px;background:linear-gradient(90deg,#23282e 0%,#4a5058 30%,#6c7178 50%,#3c5a48 75%,#2b3340 100%)}
.hero-cta{left:439px;top:386px;width:322px;height:58px;border:2px solid rgba(255,255,255,.6);background:rgba(7,146,205,.85);border-radius:14px;color:var(--white);font-weight:700;font-size:18px;letter-spacing:2.5px;display:flex;align-items:center;justify-content:center}
.dots{display:flex;gap:16px;align-items:center}
.dot{width:9px;height:9px;border-radius:50%;background:var(--white)}
.dot.ring{background:transparent;border:2px solid var(--white);width:12px;height:12px}

/* trial band */
.trial-band{left:0;top:557px;width:1200px;height:279px;background:var(--grey-band)}
.trial-circle{left:479px;top:571px;width:244px;height:244px;border-radius:50%;background:var(--white);display:flex;align-items:center;justify-content:center;text-align:center;font-size:42px;line-height:47px}

/* welcome */
.section-title{font-size:27px}
.lead{font-size:10.5px;line-height:16px;color:var(--text)}
.welcome-photo{left:160px;top:943px;width:452px;height:161px;background:linear-gradient(90deg,#8a5a35,#b07a48 40%,#3f6b33 55%,#a06b3e 80%,#7a4d2c)}

.schedule-item{position:absolute;left:668px;width:370px;height:58px;border:1px solid var(--grey-line);background:var(--white)}
.schedule-item .title{position:absolute;left:18px;top:8px;font-size:15px;font-weight:600;color:var(--blue)}
.schedule-item .desc{position:absolute;left:18px;top:33px;font-size:10px;color:var(--text)}
.schedule-date{position:absolute;right:0;top:0;width:66px;height:56px;background:#f2f2f2;display:flex;align-items:center;justify-content:center}
.date-disc{width:40px;height:40px;border-radius:50%;background:var(--white);text-align:center;font-size:15px;line-height:16px;padding-top:5px;color:var(--text-dark)}
.date-disc small{display:block;font-size:8px;line-height:10px}

/* trainer */
.trainer-band{left:0;top:1224px;width:1200px;height:334px;background:var(--grey-band);overflow:hidden}
.trainer-photo{left:243px;top:1250px;width:196px;height:308px;background:linear-gradient(180deg,#d7c1ae 0%,#c7a48a 18%,#1d1d1f 26%,#1d1d1f 70%,#3b4d66 80%,#2f3e55 100%);border-radius:40px 40px 0 0;z-index:2}
.trainer-copy{left:600px;top:1310px;width:400px;text-align:center;z-index:2}
.trainer-copy p{font-size:10.5px;line-height:17px;color:var(--text);padding:0 40px}

/* features */
.feature{position:absolute;top:1644px;width:172px;height:172px;border-radius:50%;border:2px solid #dcdcdc;text-align:center}
.feature svg{position:absolute;left:66px;top:34px}
.feature .label{position:absolute;left:0;right:0;top:92px;font-size:16px;font-weight:700;color:var(--blue);text-transform:uppercase}
.feature .sub{position:absolute;left:0;right:0;top:116px;font-size:10.5px;color:var(--text)}

/* testimonials */
.testimonial-band{left:0;top:1856px;width:1200px;height:197px;background:var(--grey-band)}
.quote-text{left:255px;top:1932px;width:718px;text-align:center;font-size:11px;line-height:18px;color:var(--text)}
.name-pill{left:562px;top:2005px;width:78px;height:19px;border-radius:10px;background:#bdbdbd;color:var(--white);font-size:9px;font-weight:700;letter-spacing:1.5px;display:flex;align-items:center;justify-content:center}

/* footer */
.site-footer{left:0;top:2053px;width:1200px;height:300px;background:var(--footer);color:var(--white)}
.footer-head{position:absolute;top:34px;font-size:11px;font-weight:700;text-transform:uppercase}
.footer-list{position:absolute;top:62px;list-style:none;font-size:10.5px;line-height:22.5px}
.field{position:absolute;left:558px;width:204px;height:37px;background:var(--footer-field);font-size:9px;font-weight:600;display:flex;align-items:center;padding-left:16px}
.subscribe{position:absolute;left:558px;top:151px;width:204px;height:36px;background:var(--orange);font-size:12px;font-weight:700;letter-spacing:2px;display:flex;align-items:center;justify-content:center}
.footer-brand{position:absolute;left:870px;top:80px;display:flex;align-items:center;gap:10px}
.footer-brand .brand-name{color:var(--white)}
.footer-brand .brand-dot{background:var(--white)}
.footer-rule{position:absolute;left:160px;top:237px;width:878px;height:1px;background:rgba(255,255,255,.2)}
.social{position:absolute;top:251px;width:28px;height:28px;border-radius:50%}
</style>
</head>
<body>

<header>
  <div class="abs brand"><span class="brand-name">Summit</span><span class="brand-dot"></span></div>
  <div class="abs call-box">
    <div class="call-icon">
      <svg width="18" height="18" viewBox="0 0 24 24"><path fill="#fff" d="M6.6 10.8a15.1 15.1 0 0 0 6.6 6.6l2.2-2.2a1 1 0 0 1 1-.25 11.4 11.4 0 0 0 3.6.57 1 1 0 0 1 1 1V20a1 1 0 0 1-1 1A17 17 0 0 1 3 4a1 1 0 0 1 1-1h3.5a1 1 0 0 1 1 1c0 1.25.2 2.45.57 3.57a1 1 0 0 1-.25 1z"/></svg>
    </div>
    <div><div class="call-label">CALL US ON</div><div class="call-number">1.800.555.0142</div></div>
  </div>
  <div class="abs search-tab">
    <svg width="10" height="10" viewBox="0 0 12 12"><circle cx="5" cy="5" r="3.6" fill="none" stroke="#fff" stroke-width="1.6"/><line x1="7.7" y1="7.7" x2="11" y2="11" stroke="#fff" stroke-width="1.8"/></svg>SEARCH
  </div>
  <nav class="abs main-nav">
    <a class="is-active">Home</a><a>Class descriptions</a><a>Gym description</a><a>Class schedules</a><a>Trainer profiles</a><a>Gym philosophy</a><a>Contact</a>
  </nav>
</header>

<section>
  <div class="abs hero" role="img" aria-label="Athlete training on parallel bars in a wood and plant filled gym"></div>
  <div class="abs hero-cta">FREE FIRST TRIAL CLASS</div>
  <div class="abs dots" style="left:538px;top:498px"><span class="dot"></span><span class="dot ring"></span><span class="dot"></span><span class="dot"></span><span class="dot"></span></div>
</section>

<section>
  <div class="abs trial-band"></div>
  <div class="btn" style="left:215px;top:678px;width:136px;height:37px">Read more</div>
  <svg class="abs" style="left:392px;top:680px" width="52" height="24" viewBox="0 0 52 24"><path d="M2 12 14 2v6h36v8H14v6z" fill="#cfcfcf"/></svg>
  <div class="abs trial-circle heading">FREE<br>FIRST<br>TRIAL<br>CLASS</div>
  <svg class="abs" style="left:750px;top:680px" width="52" height="24" viewBox="0 0 52 24"><path d="M50 12 38 2v6H2v8h36v6z" fill="#cfcfcf"/></svg>
  <div class="btn" style="left:847px;top:678px;width:155px;height:37px">Make an enquiry</div>
</section>

<section>
  <h2 class="abs heading section-title" style="left:160px;top:862px">Welcome to our site</h2>
  <p class="abs lead" style="left:160px;top:903px;width:440px">Lorem Ipsum is simply dummy text of the printing and typesetting industry. Lorem Ipsum has been the industry's standard dummy</p>
  <div class="abs welcome-photo" role="img" aria-label="Living plant wall lettering above a rack of dumbbells"></div>
  <p class="abs lead" style="left:160px;top:1118px;width:452px">Contrary to popular belief, Lorem Ipsum is not simply random text. It has roots in a piece of classical Latin literature from 45 BC, making it over 2000 years</p>
  <div class="btn" style="left:162px;top:1162px;width:108px;height:32px">Read more</div>

  <h2 class="abs heading section-title" style="left:667px;top:862px">Class schedules</h2>
  <div class="btn" style="left:960px;top:869px;width:78px;height:25px;font-size:10px">See all</div>
  <div class="schedule-item" style="top:918px"><div class="title">Tailored Fitness</div><div class="desc">Lorem Ipsum is simply dummy text of the printing</div><div class="schedule-date"><div class="date-disc">18<small>JAN</small></div></div></div>
  <div class="schedule-item" style="top:987px"><div class="title">Group Fitness</div><div class="desc">Contrary to popular belief, Lorem Ipsum</div><div class="schedule-date"><div class="date-disc">15<small>JAN</small></div></div></div>
  <div class="schedule-item" style="top:1057px"><div class="title">Outdoor Fitness</div><div class="desc">There are many variations of passages</div><div class="schedule-date"><div class="date-disc">13<small>JAN</small></div></div></div>
  <div class="schedule-item" style="top:1128px"><div class="title">Nutrition</div><div class="desc">But I must explain to you how all this mistaken</div><div class="schedule-date"><div class="date-disc">11<small>JAN</small></div></div></div>
</section>

<section>
  <div class="abs trainer-band">
    <svg width="1200" height="334" viewBox="0 0 1200 334" style="position:absolute;left:0;top:0">
      <polygon points="0,186 0,334 1200,334 1200,330" fill="var(--blue)"/>
      <circle cx="800" cy="272" r="232" fill="#fafafa"/>
      <polygon points="560,258 1040,300 1040,334 560,334" fill="#d8eef7" opacity=".8"/>
      <polygon points="1020,298 1200,328 1200,334 1020,334" fill="var(--blue)"/>
    </svg>
  </div>
  <div class="abs trainer-photo" role="img" aria-label="Portrait of a trainer in a black t-shirt"></div>
  <div class="abs trainer-copy">
    <h2 class="heading section-title" style="font-size:25px">Trainer profiles</h2>
    <div style="font-size:14px;font-weight:700;color:var(--blue);margin:16px 0 12px">DANIEL REYES</div>
    <p>On the other hand, we denounce with righteous indignation and dislike men who are so beguiled and demoralized by the charms of pleasure of the moment, so blinded by desire, that they cannot foresee the pain and trouble that are bound to ensue; and equal blame belongs to those who fail in their duty through weakness of will,</p>
  </div>
  <div class="abs dots" style="left:758px;top:1520px;gap:14px;z-index:2"><span class="dot" style="background:#bbb"></span><span class="dot ring" style="border-color:#bbb"></span><span class="dot" style="background:#bbb"></span><span class="dot" style="background:#bbb"></span></div>
</section>

<section>
  <h2 class="abs heading section-title" style="left:0;width:1200px;text-align:center;top:1582px">Our features</h2>
  <div class="feature" style="left:185px">
    <svg width="40" height="40" viewBox="0 0 40 40"><circle cx="20" cy="8" r="5" fill="#8a8a8a"/><rect x="4" y="14" width="4" height="14" fill="#8a8a8a"/><rect x="32" y="14" width="4" height="14" fill="#8a8a8a"/><rect x="8" y="19" width="24" height="4" fill="#8a8a8a"/><rect x="13" y="15" width="14" height="14" fill="#8a8a8a"/><rect x="14" y="30" width="5" height="9" fill="#8a8a8a"/><rect x="21" y="30" width="5" height="9" fill="#8a8a8a"/></svg>
    <div class="label">Get active</div><div class="sub">On the other hand</div>
  </div>
  <div class="feature" style="left:403px">
    <svg width="40" height="40" viewBox="0 0 40 40"><polygon points="20,3 25,15 38,15 28,24 32,37 20,29 8,37 12,24 2,15 15,15" fill="none" stroke="#8a8a8a" stroke-width="2.5" stroke-linejoin="round"/></svg>
    <div class="label">Reviews</div><div class="sub">On the other hand</div>
  </div>
  <div class="feature" style="left:623px">
    <svg width="40" height="40" viewBox="0 0 40 40"><polygon points="36,4 4,18 20,20 22,36" fill="#8a8a8a"/></svg>
    <div class="label">Find location</div><div class="sub">On the other hand</div>
  </div>
  <div class="feature" style="left:846px">
    <svg width="40" height="40" viewBox="0 0 40 40"><rect x="16" y="3" width="8" height="34" fill="#8a8a8a"/><rect x="3" y="16" width="34" height="8" fill="#8a8a8a"/></svg>
    <div class="label">Get more</div><div class="sub">On the other hand</div>
  </div>
</section>

<section>
  <div class="abs testimonial-band"></div>
  <h2 class="abs heading section-title" style="left:0;width:1200px;text-align:center;top:1880px">Testimonials</h2>
  <svg class="abs" style="left:140px;top:1936px" width="24" height="32" viewBox="0 0 24 32"><polyline points="18,2 6,16 18,30" fill="none" stroke="#b5b5b5" stroke-width="3"/></svg>
  <svg class="abs" style="left:1036px;top:1936px" width="24" height="32" viewBox="0 0 24 32"><polyline points="6,2 18,16 6,30" fill="none" stroke="#b5b5b5" stroke-width="3"/></svg>
  <svg class="abs" style="left:216px;top:1924px" width="28" height="22" viewBox="0 0 28 22"><path d="M2 22V12Q2 3 11 0v4Q7 6 7 11h5v11zM16 22V12q0-9 9-12v4q-4 2-4 7h5v11z" fill="#d0d0d0"/></svg>
  <p class="abs quote-text">On the other hand, we denounce with righteous indignation and dislike men who are so beguiled and demoralized by the charms of pleasure of the moment, so blinded by desire, that they cannot foresee the pain and trouble that are bound to ensue; and equal blame belongs to those who fail in their duty through weakness of will,</p>
  <div class="abs name-pill">MARCUS</div>
</section>

<footer class="abs site-footer">
  <div class="footer-head" style="left:160px">Menu</div>
  <ul class="footer-list" style="left:160px"><li>Home</li><li>Class descriptions</li><li>Gym description</li><li>Class schedules</li><li>Trainer profiles</li><li>Gym philosophy</li><li>Contact</li></ul>
  <div class="footer-head" style="left:355px">Contact us</div>
  <ul class="footer-list" style="left:355px"><li>47 Cedar Lane</li><li>Brookfield, OR 97021</li><li>1.800.555.0142</li><li>hello@summitbodyform.com</li></ul>
  <div class="footer-head" style="left:557px">Newsletter signup!</div>
  <div class="field" style="top:61px">NAME</div>
  <div class="field" style="top:104px">E MAIL</div>
  <div class="subscribe">SUBSCRIBE</div>
  <div class="footer-brand"><span class="brand-name">Summit</span><span class="brand-dot"></span></div>
  <div class="footer-rule"></div>
  <div style="position:absolute;left:160px;top:258px;font-size:10px;font-weight:600">Follow us on</div>
  <div class="social" style="left:229px;background:#2f5aa8"></div>
  <div class="social" style="left:261px;background:#2aa3e0"></div>
  <div class="social" style="left:297px;background:var(--orange)"></div>
  <div style="position:absolute;right:162px;top:258px;font-size:10px;font-weight:600">Copyrights @ 2015 All Rights Reserved</div>
</footer>

</body>
</html>
```